Hollow Thicket, a 3d voxel survival video game needs a card for gaming conventions

I am the lead developer for Hollow Thicket http://www.HollowThicket.example and need a business card to hand out at an indie gaming convention
The card would need to include the game name, website url, my name, position (Lead Developer), e-mail and phone number
The game is a 3d, voxel (with smooth terrain) based survival game with guns and wildlife. The main icon of the game would likely be a grizzly bear but I am willing to accept other designs too.
Attached is a media kit for the game with some images you can use but don't have to its just what little art I can provide. Anything on the website or from the video game can also be used. unrelated art can also be used.
Target Market(s)
Indie Developers/publishers at conferences
Industry/Entity Type
Games
Contact Information for Business Card
Name: Corin Waldrick
Position: Lead Developer
E-mail: Pale_Kettle@mailbox.example
Phone number: 555-372-1186

```html
<!DOCTYPE html>
<html lang="en">
<head>
<meta charset="utf-8">
<title>Hollow Thicket – Business Card</title>
<link rel="stylesheet" href="https://fonts.googleapis.com/css2?family=Open+Sans:wght@400;600;700&display=swap">
<style>
  :root {
    --backdrop-top: #2a2a2a;
    --backdrop-bottom: #050505;
    --card-white: #ffffff;
    --brand-red: #8c1a12;
    --brand-gold: #9a7a3a;
    --ink: #2b2b2b;
    --icon-red: #a3160f;
    --fur-light: #a87a55;
    --fur-dark: #4a2e1c;
    --parchment-light: #efe6c8;
    --parchment-mid: #b8a878;
    --parchment-dark: #3a3420;
  }
  * { margin: 0; padding: 0; box-sizing: border-box; }
  html, body { width: 1200px; height: 900px; overflow: hidden; }
  body {
    background: linear-gradient(180deg, var(--backdrop-top) 0%, #1a1a1a 45%, var(--backdrop-bottom) 100%);
    font-family: "Open Sans", Arial, sans-serif;
    position: relative;
  }
  .card {
    position: absolute;
    top: 306px;
    width: 440px;
    height: 271px;
    border-radius: 12px;
    overflow: hidden;
  }
  .card--front { left: 149px; background: var(--card-white); }
  .card--back { left: 608px; }

  .game-name {
    position: absolute;
    left: 0; right: 0;
    text-align: center;
    font-weight: 700;
    color: var(--brand-red);
    letter-spacing: 1px;
    text-transform: uppercase;
    line-height: 1;
    white-space: nowrap;
  }
  .card--front .game-name { top: 54px; font-size: 32px; }
  .card--back .game-name { top: 117px; font-size: 38px; }

  .bear-photo { position: absolute; }
  .card--front .bear-photo {
    left: 0; top: 106px; width: 118px; height: 165px;
    background: linear-gradient(180deg, var(--fur-light) 0%, var(--fur-dark) 70%, #f4f0ec 100%);
    border-radius: 0 40px 0 0;
  }
  .card--back .backdrop-pattern {
    position: absolute; inset: 0;
    background: radial-gradient(ellipse at 60% 55%, var(--parchment-light) 0%, var(--parchment-mid) 50%, var(--parchment-dark) 100%);
  }
  .card--back .bear-photo {
    left: 0; top: 56px; width: 194px; height: 215px;
    background: linear-gradient(180deg, var(--fur-light) 0%, #7a5236 55%, var(--fur-dark) 100%);
    border-radius: 60px 70px 0 0;
  }

  .contact {
    position: absolute;
    left: 0; right: 0;
    text-align: center;
    color: var(--ink);
    white-space: nowrap;
  }
  .person-name {
    top: 139px;
    font-size: 15px;
    font-weight: 600;
    text-transform: uppercase;
  }
  .person-name .first { color: var(--brand-red); }
  .person-name .last { color: var(--brand-gold); }
  .person-role { top: 158px; font-size: 12.5px; }
  .contact-line { font-size: 12.5px; display: flex; justify-content: center; align-items: center; gap: 4px; }
  .contact-line svg { width: 9px; height: 9px; fill: var(--icon-red); }
  .phone { top: 198px; }
  .email { top: 214px; }
  .website { top: 232px; font-size: 11.5px; color: var(--brand-red); }
</style>
</head>
<body>
  <section class="card card--front">
    <div class="game-name">Hollow Thicket</div>
    <div class="bear-photo" role="img" aria-label="Photo of a roaring grizzly bear"></div>
    <div class="contact person-name"><span class="first">Corin</span> <span class="last">Waldrick</span></div>
    <div class="contact person-role">Lead Developer</div>
    <div class="contact contact-line phone">
      <svg viewBox="0 0 10 10" aria-hidden="true"><path d="M1 3.5 C1 2 2.5 1 5 1 S9 2 9 3.5 L7 4 L6.5 3 H3.5 L3 4 Z M2.5 4.5 H7.5 L8.5 9 H1.5 Z"/></svg>
      <span>555-372-1186</span>
    </div>
    <div class="contact contact-line email">
      <svg viewBox="0 0 10 10" aria-hidden="true"><path d="M0.5 2 H9.5 V8 H0.5 Z" /><path d="M0.5 2 L5 5.5 L9.5 2" stroke="#fff" stroke-width="0.9" fill="none"/></svg>
      <span>Pale_Kettle@mailbox.example</span>
    </div>
    <div class="contact website">http://www.HollowThicket.example</div>
  </section>

  <section class="card card--back">
    <div class="backdrop-pattern" role="img" aria-label="Parchment background with faint repeated game name pattern"></div>
    <div class="bear-photo" role="img" aria-label="Photo of a standing grizzly bear"></div>
    <div class="game-name">Hollow Thicket</div>
  </section>
</body>
</html>
```